Nanny Share Ecommerce Website for Finding Childcare and Parents who need Childcare BrightPramHub.net

Our company needs an ecommerce website (BrightPramHub.net) for a US subscription based service strictly for nanny sharing that connects families and caregivers. The website would allow families to connect with one another as well as to search for nannies. The service would be searchable for other families by location (by radius or zip code), children demographic (age range/gender/special needs), days of week or times, after school care, school closure days (holidays), etc. The service would also be searchable for nannies based on gender, provider age range, years experience, language, hourly rate, transportation available, certification (CPR first aid), education etc. The search fields would be searchable and sortable and allow to connect with the provider (after paying subscription fee). The service would be similar to tendlyfolk.net in that it would allow for families and caregivers to post photos as well as a short bio of the themselves. There would also be a feedback/star rating mechanism to rate caregivers who have performed work for families (viewable to public). The service would be free for nannies to post their bios and only a subscription based service for families to connect with other families or with caregivers (able to view bio but need service to connect). There will be a short bio on the benefits of nanny sharing (reduced cost, increased flexibility for parents, reduced illness, increased socialization with other children vs. sole nanny), as well as Q&A section with best practices.

Target Market(s)

Families, Nannies

Industry/Entity Type

Childcare

Logo Text

Bright Pram Hub

Coding

Coded - Design and coding required

Number of Pages Required

5+ page

Requirements
Must have
• Searchable (need to be able to search for families as well as nannies), responsive, functional, easy to use, add value to families and nannies. Needs to be able to collect payment for subscription.
Nice to have
• Optimized for mobile, SEO optimized

```html
<!DOCTYPE html>
<html lang="en">
<head>
<meta charset="utf-8">
<title>Bright Pram Hub – Nanny Sharing</title>
<link rel="stylesheet" href="https://fonts.googleapis.com/css2?family=Oswald:wght@500;600&family=PT+Sans:wght@400;700&display=swap">
<style>
:root{
  --pink:#fb0a84;
  --green:#14b293;
  --ink:#1c1c1c;
  --text:#444;
  --muted:#9b9b9b;
  --mint:#e3f2ee;
  --grey-band:#efefef;
  --pill:#ececec;
  --footer:#0e0e10;
  --white:#fff;
}
*{box-sizing:border-box;margin:0;padding:0}
html,body{width:1200px;height:3285px;overflow:hidden}
body{position:relative;background:var(--white);font-family:"PT Sans",Arial,sans-serif;color:var(--text)}
.abs{position:absolute}
.heading{font-family:"Oswald",Impact,sans-serif;font-weight:600;color:var(--ink);letter-spacing:.5px}
.accent-pink{color:var(--pink)}
.accent-green{color:var(--green)}
.btn{position:absolute;display:flex;align-items:center;justify-content:center;border-radius:30px;font-family:"PT Sans",Arial,sans-serif;font-weight:700;text-transform:uppercase;color:var(--white)}
.btn-pink{background:var(--pink)}
.btn-green{background:var(--green)}
.btn-sm{height:36px;font-size:12px}

/* header */
.site-header{position:absolute;left:0;top:0;width:1200px;height:120px}
.brand{position:absolute;left:72px;top:38px;display:flex;align-items:center;gap:12px;font-family:"PT Sans",Arial,sans-serif;font-weight:700;font-size:30px;line-height:40px;color:var(--ink)}
.brand-dot{width:22px;height:22px;border-radius:50%;background:var(--pink)}
.icon-circle{position:absolute;width:46px;height:46px;border-radius:50%;display:flex;align-items:center;justify-content:center}
.contact-text{position:absolute;font-size:15px;line-height:19px;color:var(--ink)}
.phone-big{font-weight:700;font-size:24px;line-height:28px}
.lang{position:absolute;left:997px;top:40px;width:131px;height:42px;border-radius:21px;background:var(--pill);font-size:14px;color:var(--ink);display:flex;align-items:center;padding-left:20px}
.lang svg{position:absolute;right:18px;top:15px}

/* nav */
.main-nav{position:absolute;left:0;top:120px;width:1200px;height:66px;background:var(--pink)}
.nav-link{position:absolute;top:22px;font-size:17px;color:var(--white)}
.btn-login{left:905px;top:13px;width:80px;height:40px;border:2px solid rgba(255,255,255,.8);font-size:13px;text-transform:none}
.btn-register{left:992px;top:11px;width:136px;height:44px;background:var(--white);color:var(--ink);font-size:13px;text-transform:none;border:2px solid #ddd}

/* hero */
.hero{position:absolute;left:0;top:186px;width:1200px;height:504px;background:var(--mint);overflow:hidden}
.hero-photo{position:absolute;left:0;top:0;width:1200px;height:504px;background:linear-gradient(120deg,#f4efe8 0%,#e8d9c8 35%,#b9c9d9 65%,#8ea4bd 100%);clip-path:polygon(515px 0,1200px 0,1200px 504px,440px 504px,440px 160px)}
.hero-cut{position:absolute;left:0;top:0}
.hero-title{position:absolute;left:135px;top:162px;font-family:"PT Sans",Arial,sans-serif;font-weight:700;font-size:46px;color:#333}
.dot{position:absolute;top:363px;width:11px;height:11px;border-radius:50%;background:#888}

/* welcome */
.video-thumb{position:absolute;left:72px;top:712px;width:362px;height:230px;background:linear-gradient(135deg,#6c6a6a,#a39a94 50%,#4f4d4e)}
.welcome-title{position:absolute;left:451px;top:716px;font-size:34px;line-height:50px}
.body-copy{font-size:14px;line-height:24px;color:#333}

/* benefits */
.benefits{position:absolute;left:0;top:1000px;width:1200px;height:518px;background:linear-gradient(100deg,#ecebe8 0%,#f5f5f3 45%,#e9ece6 100%)}
.benefits-photo{position:absolute;left:613px;top:121px;width:475px;height:316px;background:linear-gradient(130deg,#8a7b6e,#c9b39e 45%,#6f8eb0 80%,#4d5f7c)}
.benefit-item{position:absolute;left:102px;font-size:16px;color:#333;display:flex;align-items:center;gap:14px}
.tick{width:18px;height:18px;border-radius:50%;background:var(--green);display:flex;align-items:center;justify-content:center}

/* services */
.section-title{position:absolute;left:0;width:1200px;text-align:center;font-size:37px}
.service-card{position:absolute;top:1638px;width:324px}
.service-photo{width:324px;height:344px}
.service-name{margin-top:20px;text-align:center;font-family:"Oswald",Impact,sans-serif;font-weight:600;font-size:38px;color:var(--muted);letter-spacing:1px}
.service-copy{margin:8px 8px 0;text-align:center;font-size:13.5px;line-height:24px;color:#444}
.service-card .btn{position:static;margin:22px auto 0;width:122px}

/* feedback */
.feedback{position:absolute;left:0;top:2285px;width:1200px;height:365px;background:var(--grey-band)}
.quote-badge{position:absolute;left:574px;top:120px;width:52px;height:52px;border-radius:50%;background:var(--green);display:flex;align-items:center;justify-content:center;color:var(--white);font-family:Georgia,serif;font-weight:700;font-size:40px;line-height:1;padding-top:18px}
.quote{position:absolute;left:175px;top:190px;width:850px;text-align:center;font-size:14px;line-height:24px;color:#444}
.stars{position:absolute;left:535px;top:282px;display:flex;gap:10px}

/* faq */
.faq-row{position:absolute;width:469px;height:48px;border-radius:24px;background:var(--pill);display:flex;align-items:center;justify-content:space-between;padding:0 26px;font-size:14px;color:#333}
.faq-row.open{background:var(--pink);color:var(--white)}
.faq-sign{font-size:22px;color:var(--pink);font-weight:700}
.faq-row.open .faq-sign{color:var(--white)}
.faq-answer{position:absolute;left:107px;top:2818px;width:469px;height:74px;background:var(--pill);border-radius:0 0 20px 20px;padding:26px 26px 0;font-size:13.5px;line-height:19px;color:#444}

/* contact + footer */
.contact-band{position:absolute;left:0;top:3050px;width:1200px;height:88px;background:var(--green);color:var(--white)}
.contact-title{position:absolute;left:140px;top:22px;font-family:"Oswald",Impact,sans-serif;font-weight:600;font-size:31px;color:var(--white)}
.site-footer{position:absolute;left:0;top:3138px;width:1200px;height:147px;background:var(--footer);color:var(--white)}
.footer-nav{position:absolute;left:0;top:29px;width:1200px;display:flex;justify-content:center;gap:30px;font-size:15px}
.social{position:absolute;left:515px;top:66px;display:flex;gap:22px}
.social span{width:20px;height:20px;border-radius:50%;background:var(--white)}
.copyright{position:absolute;left:0;top:104px;width:1200px;text-align:center;font-size:12.5px;color:#cfcfcf}
</style>
</head>
<body>

<header class="site-header">
  <div class="brand"><span class="brand-dot"></span>Bright Pram Hub</div>
  <div class="icon-circle" style="left:487px;top:38px;background:var(--pink)">
    <svg width="18" height="22" viewBox="0 0 18 22"><path d="M9 0C4 0 0 4 0 9c0 6 9 13 9 13s9-7 9-13c0-5-4-9-9-9z" fill="#fff"/><circle cx="9" cy="9" r="3.5" fill="#fb0a84"/></svg>
  </div>
  <div class="contact-text" style="left:550px;top:41px;font-size:14px">123 , Lorium Ipsum Dolor,<br>Amit, AU- 2345.</div>
  <div class="icon-circle" style="left:740px;top:36px;background:var(--green)">
    <svg width="20" height="20" viewBox="0 0 24 24"><path d="M6.6 10.8a15 15 0 006.6 6.6l2.2-2.2c.3-.3.7-.4 1-.2 1.1.4 2.3.6 3.6.6.6 0 1 .4 1 1V20c0 .6-.4 1-1 1A17 17 0 013 4c0-.6.4-1 1-1h3.5c.6 0 1 .4 1 1 0 1.3.2 2.5.6 3.6.1.3 0 .7-.2 1z" fill="#fff"/></svg>
  </div>
  <div class="contact-text" style="left:800px;top:34px;font-size:14px">Call Us</div>
  <div class="contact-text phone-big" style="left:800px;top:54px">1-800 555 0142</div>
  <div class="lang">English
    <svg width="14" height="10" viewBox="0 0 14 10"><path d="M1 1l6 6 6-6" stroke="#222" stroke-width="2.4" fill="none"/></svg>
  </div>
</header>

<nav class="main-nav">
  <span class="nav-link" style="left:74px">Home</span>
  <span class="nav-link" style="left:155px">Child Care</span>
  <span class="nav-link" style="left:270px">House Keeping</span>
  <span class="nav-link" style="left:427px">Testimonials</span>
  <span class="nav-link" style="left:560px">How it Works</span>
  <span class="nav-link" style="left:698px">FAQ</span>
  <span class="nav-link" style="left:762px">Support</span>
  <span class="btn btn-login">Login</span>
  <span class="btn btn-register">Register Now</span>
</nav>

<section class="hero">
  <div class="hero-photo" role="img" aria-label="Photo of a caregiver reading a book with a young girl"></div>
  <svg class="hero-cut" width="1200" height="504" viewBox="0 0 1200 504"><polygon points="0,404 1200,504 0,504" fill="#fff"/></svg>
  <h1 class="hero-title">LORIUM IPSUM</h1>
  <span class="btn btn-green" style="left:135px;top:241px;width:172px;height:55px;font-size:19px">Find Care</span>
  <span class="btn btn-pink" style="left:328px;top:241px;width:221px;height:55px;font-size:19px">Find Nannies</span>
  <span class="dot" style="left:144px"></span>
  <span class="dot" style="left:172px;background:var(--pink)"></span>
  <span class="dot" style="left:201px"></span>
</section>

<section class="welcome">
  <div class="video-thumb" role="img" aria-label="Video still of a mother and child at home"></div>
  <svg class="abs" style="left:219px;top:793px" width="68" height="68" viewBox="0 0 68 68"><circle cx="34" cy="34" r="31" stroke="#fff" stroke-width="3" fill="none"/><path d="M27 21l20 13-20 13z" stroke="#fff" stroke-width="3" fill="none" stroke-linejoin="round"/></svg>
  <h2 class="heading welcome-title">WELCOME TO <span class="accent-pink">BRIGHT PRAM HUB</span></h2>
  <p class="abs body-copy" style="left:453px;top:770px;width:685px">Aliquam molestie, mi et imperdiet euismod, dui purus auctor tellus, et interdum lacus lectus et ante. Sed accumsan sollicitudin sapien, sit amet adipiscing turpis gravida ac. In congue, neque ac lobortis volutpat, libero mauris varius mi, vitae suscipit ipsum ligula vitae risus. Duis aliquam nibh a dui iaculis viverra id a velit. Vivamus egestas risus in magna varius commodo.</p>
  <span class="btn btn-pink btn-sm" style="left:453px;top:884px;width:121px">Read More</span>
</section>

<section class="benefits">
  <h2 class="section-title heading" style="top:34px">BENEFITS OF <span class="accent-green">NANNY SHARING</span></h2>
  <div class="benefit-item" style="top:184px"><span class="tick"><svg width="10" height="8" viewBox="0 0 10 8"><path d="M1 4l3 3 5-6" stroke="#fff" stroke-width="2" fill="none"/></svg></span>Reduced cost</div>
  <div class="benefit-item" style="top:228px"><span class="tick"><svg width="10" height="8" viewBox="0 0 10 8"><path d="M1 4l3 3 5-6" stroke="#fff" stroke-width="2" fill="none"/></svg></span>Increased flexibility for parents</div>
  <div class="benefit-item" style="top:272px"><span class="tick"><svg width="10" height="8" viewBox="0 0 10 8"><path d="M1 4l3 3 5-6" stroke="#fff" stroke-width="2" fill="none"/></svg></span>Rreduced illness</div>
  <div class="benefit-item" style="top:316px"><span class="tick"><svg width="10" height="8" viewBox="0 0 10 8"><path d="M1 4l3 3 5-6" stroke="#fff" stroke-width="2" fill="none"/></svg></span>Iincreased socialization with other children vs. sole nanny</div>
  <span class="btn btn-green btn-sm" style="left:105px;top:364px;width:121px">Read More</span>
  <div class="benefits-photo" role="img" aria-label="Photo of a woman and a girl drawing together at a table"></div>
</section>

<section class="services">
  <h2 class="section-title heading" style="top:1555px">OUR <span class="accent-pink">SERVICES</span></h2>
  <svg class="abs" style="left:434px;top:1566px" width="14" height="22" viewBox="0 0 14 22"><path d="M11 2L3 11l8 9" stroke="#111" stroke-width="4" fill="none"/></svg>
  <svg class="abs" style="left:752px;top:1566px" width="14" height="22" viewBox="0 0 14 22"><path d="M3 2l8 9-8 9" stroke="#111" stroke-width="4" fill="none"/></svg>

  <article class="service-card" style="left:98px">
    <div class="service-photo" role="img" aria-label="Photo of a mother holding a smiling toddler" style="background:linear-gradient(135deg,#e9e4df,#c9a58d 50%,#5c4236)"></div>
    <h3 class="service-name">CHILD CARE</h3>
    <p class="service-copy">Sit amet eget ex sed porta. Nec lobortis mauris malesuada porttitor duis eleifend felis integer turpis lacus donec lacus amet eu. Enim ac velit. Urna velit vel. Ut elit venenatis.</p>
    <span class="btn btn-pink btn-sm">Read More</span>
  </article>

  <article class="service-card" style="left:440px">
    <div class="service-photo" role="img" aria-label="Photo of a carer beside an elderly woman" style="background:linear-gradient(135deg,#27486a,#6d8aa3 45%,#d8cfc7 75%,#8a8d86)"></div>
    <h3 class="service-name">SENIOR CARE</h3>
    <p class="service-copy">Sit amet eget ex sed porta. Nec lobortis mauris malesuada porttitor duis eleifend felis integer turpis lacus donec lacus amet eu. Enim ac velit. Urna velit vel. Ut elit venenatis.</p>
    <span class="btn btn-pink btn-sm">Read More</span>
  </article>

  <article class="service-card" style="left:782px">
    <div class="service-photo" role="img" aria-label="Photo of a woman ironing clothes at home" style="background:linear-gradient(135deg,#c9c9c9,#e7e4e0 40%,#7fa3c8 70%,#9c8d84)"></div>
    <h3 class="service-name">HOME CARE</h3>
    <p class="service-copy">Sit amet eget ex sed porta. Nec lobortis mauris malesuada porttitor duis eleifend felis integer turpis lacus donec lacus amet eu. Enim ac velit. Urna velit vel. Ut elit venenatis.</p>
    <span class="btn btn-pink btn-sm">Read More</span>
  </article>
</section>

<section class="feedback">
  <h2 class="section-title heading" style="top:56px">FEEDBACK</h2>
  <div class="quote-badge">”</div>
  <svg class="abs" style="left:90px;top:196px" width="14" height="22" viewBox="0 0 14 22"><path d="M11 2L3 11l8 9" stroke="#111" stroke-width="4" fill="none"/></svg>
  <svg class="abs" style="left:1088px;top:196px" width="14" height="22" viewBox="0 0 14 22"><path d="M3 2l8 9-8 9" stroke="#111" stroke-width="4" fill="none"/></svg>
  <p class="quote">"Bibendum nulla pede aliquam vestibulum erat. Pellentesque lacus nisl sodales felis laoreet fringilla penatibus mus. Ipsum purus orci. Risus orci inceptos porta ornare mauris. Porta non nunc. Lacus at convallis vestibulum vel justo. Magna turpis velit et malesuada moles- tie pretium eget nunc faucibus dolor in metus lorem pulvinar."</p>
  <div class="stars">
    <svg width="18" height="18" viewBox="0 0 24 24"><path d="M12 2l3 7h7l-5.5 4.5 2 7.5-6.5-4.5-6.5 4.5 2-7.5L2 9h7z" fill="#14b293"/></svg>
    <svg width="18" height="18" viewBox="0 0 24 24"><path d="M12 2l3 7h7l-5.5 4.5 2 7.5-6.5-4.5-6.5 4.5 2-7.5L2 9h7z" fill="#14b293"/></svg>
    <svg width="18" height="18" viewBox="0 0 24 24"><path d="M12 2l3 7h7l-5.5 4.5 2 7.5-6.5-4.5-6.5 4.5 2-7.5L2 9h7z" fill="#14b293"/></svg>
    <svg width="18" height="18" viewBox="0 0 24 24"><path d="M12 2l3 7h7l-5.5 4.5 2 7.5-6.5-4.5-6.5 4.5 2-7.5L2 9h7z" fill="#14b293"/></svg>
    <svg width="18" height="18" viewBox="0 0 24 24"><path d="M12 2l3 7h7l-5.5 4.5 2 7.5-6.5-4.5-6.5 4.5 2-7.5L2 9h7z" fill="#222"/></svg>
  </div>
</section>

<section class="faq">
  <h2 class="section-title heading" style="top:2682px">FAQ</h2>
  <div class="faq-answer">Nec lobortis mauris malesuada porttitor duis eleifend felis integer turpis lacus donec lacus amet eu.</div>
  <div class="faq-row open" style="left:107px;top:2788px">Pharetra eros libero. Morbi erat porta ?<span class="faq-sign">−</span></div>
  <div class="faq-row" style="left:107px;top:2902px">Pharetra eros libero. Morbi erat porta ?<span class="faq-sign">+</span></div>
  <div class="faq-row" style="left:107px;top:2957px">Pharetra eros libero. Morbi erat porta ?<span class="faq-sign">+</span></div>
  <div class="faq-row" style="left:624px;top:2788px">Nec lobortis mauris malesuada ?<span class="faq-sign">+</span></div>
  <div class="faq-row" style="left:624px;top:2845px">Sit amet eget ex sed porta. Nec lobortis mauris ?<span class="faq-sign">+</span></div>
  <div class="faq-row" style="left:624px;top:2902px">Nec lobortis mauris malesuada ?<span class="faq-sign">+</span></div>
  <div class="faq-row" style="left:624px;top:2957px">Sit amet eget lobortis mauris malesuada ?<span class="faq-sign">+</span></div>
</section>

<section class="contact-band">
  <h2 class="contact-title">CONTACT US</h2>
  <svg class="abs" style="left:458px;top:32px" width="18" height="24" viewBox="0 0 18 22"><path d="M9 0C4 0 0 4 0 9c0 6 9 13 9 13s9-7 9-13c0-5-4-9-9-9z" fill="#fff"/><circle cx="9" cy="9" r="3.5" fill="#14b293"/></svg>
  <div class="contact-text" style="left:512px;top:25px;color:#fff;font-size:15px">123 Lorium ipsumdolor.<br>amit,AU - 3456</div>
  <svg class="abs" style="left:796px;top:33px" width="22" height="22" viewBox="0 0 24 24"><path d="M6.6 10.8a15 15 0 006.6 6.6l2.2-2.2c.3-.3.7-.4 1-.2 1.1.4 2.3.6 3.6.6.6 0 1 .4 1 1V20c0 .6-.4 1-1 1A17 17 0 013 4c0-.6.4-1 1-1h3.5c.6 0 1 .4 1 1 0 1.3.2 2.5.6 3.6.1.3 0 .7-.2 1z" fill="#fff"/></svg>
  <div class="contact-text" style="left:845px;top:18px;color:#fff;font-size:15px">Call Us</div>
  <div class="contact-text phone-big" style="left:845px;top:38px;color:#fff">1-800 555 0187</div>
</section>

<footer class="site-footer">
  <nav class="footer-nav">
    <span>Home</span><span>Child Care</span><span>House Keeping</span><span>Testimonials</span><span>How it Works</span><span>FAQ</span><span>Support</span>
  </nav>
  <div class="social" aria-label="Social links">
    <span></span><span></span><span></span><span></span><span></span>
  </div>
  <p class="copyright">Copyright © 2018. Company Name .All Right Reserved &nbsp; | &nbsp; Privacy Policy &nbsp; | &nbsp; Terms</p>
</footer>

</body>
</html>
```